A start up special flyer design!

Hi All - Have updated the attachment content - This is the info required for the designs.
I need a catchy flyer to send out to a few areas to advertise the start of my plumbing business!
The flyer will contain an offer for customers, which will need to have some key details on it. See attached. Feel free to fit these criteria into the flyer given your knowledge on design and messaging principles. Key thing to get across to customers is the discount and special offer, and that it is a start up offer.
I have a logo that needs to be on the flyer as well - let me know what format you require and I will send through to you.
The color scheme needs to be blue / grey / black / white.
Let me know if you have any questions.
I

```html
<!DOCTYPE html>
<html lang="en">
<head>
<meta charset="utf-8">
<title>Marcus Plumbing – Start Up Offer Flyer</title>
<link href="https://fonts.googleapis.com/css2?family=Roboto+Condensed:ital,wght@0,400;0,700;1,400;1,700&display=swap" rel="stylesheet">
<style>
  :root{
    --navy:#1f4a8f;
    --navy-dark:#163a75;
    --sky:#9fd3ff;
    --orange:#f39a3d;
    --ink:#141414;
    --paper:#ffffff;
    --mist-top:#e9edf1;
    --mist-bottom:#c9d1da;
    --stage:#ececec;
  }
  *{box-sizing:border-box;margin:0;padding:0}
  html,body{width:1200px;height:1000px;overflow:hidden;background:var(--stage)}
  body{font-family:"Roboto Condensed",Arial,sans-serif;position:relative}
  .flyer{position:absolute;left:285px;top:55px;width:630px;height:890px;overflow:hidden;
    background:linear-gradient(180deg,var(--mist-top) 0%,#dfe4ea 55%,var(--mist-bottom) 85%);
    box-shadow:0 4px 14px rgba(0,0,0,.25)}
  .flyer__accent{position:absolute;left:0;top:0}
  .brand{position:absolute;left:266px;top:78px;width:320px;color:var(--ink);font-weight:700;
    font-size:56px;line-height:.95;text-transform:uppercase;letter-spacing:-1px}
  .photo{position:absolute}
  .photo--plumber{left:35px;top:18px;width:220px;height:452px;
    background:linear-gradient(180deg,#e6e8ea 0%,#3f6fb0 30%,#2d5a9a 70%,#a5855a 100%);
    border-radius:60px 60px 0 0}
  .photo--thumb{top:305px;width:173px;height:130px;border:4px solid var(--paper)}
  .photo--under-sink{left:242px;background:linear-gradient(135deg,#dfe6ee,#3b64a8 60%,#2a2a2a)}
  .photo--pipe{left:427px;background:linear-gradient(135deg,#f2f4f6,#b8c2cc 50%,#c9463d 75%,#e6c0a0)}
  .panel{position:absolute;top:472px;width:298px;height:251px;background:var(--navy);color:var(--paper)}
  .panel--offer{left:0;border-radius:0 16px 16px 0}
  .panel--services{left:332px;border-radius:16px 0 0 16px}
  .panel__frame{position:absolute;inset:8px;border:2px dashed rgba(255,255,255,.85)}
  .panel--offer .panel__frame{left:-4px;border-radius:0 12px 12px 0}
  .panel--services .panel__frame{right:-4px;border-radius:12px 0 0 12px}
  .panel__tab{position:absolute;top:-7px;height:40px;background:var(--orange);color:var(--paper);
    font-weight:700;font-size:27px;line-height:40px;padding:0 14px;border-radius:5px 5px 0 0}
  .panel--offer .panel__tab{left:37px}
  .panel--services .panel__tab{left:39px}
  .checklist{position:absolute;top:50px;left:14px;right:10px;list-style:none}
  .checklist li{position:relative;padding-left:28px;font-size:20px;line-height:24px;margin-bottom:24px}
  .checklist svg{position:absolute;left:0;top:-3px}
  .hl{color:var(--sky);font-weight:700}
  .lead{font-size:23px}
  .panel--services .checklist li{font-weight:700;color:#cfe8ff}
  .footer{position:absolute;left:0;right:0;bottom:0;height:117px;background:var(--paper)}
  .footer__rule{position:absolute;left:0;right:0;top:773px;height:6px;background:var(--navy)}
  .cta{position:absolute;left:120px;top:752px;width:390px;height:49px;background:#111;color:var(--paper);
    border-radius:6px;text-align:center;font-size:16.5px;line-height:21px;padding-top:3px;
    box-shadow:0 6px 10px rgba(0,0,0,.3)}
  .cta .hl{color:var(--sky)}
  .terms{position:absolute;left:37px;top:823px;font-size:11px;line-height:14px;font-style:italic;color:var(--ink)}
  .terms b{font-weight:700}
  .contact{position:absolute;right:35px;top:815px;text-align:right;color:var(--ink)}
  .contact__phone{font-weight:700;font-size:27px;display:flex;align-items:center;gap:6px;justify-content:flex-end}
  .contact__line{font-size:12px;line-height:15px}
</style>
</head>
<body>
<main class="flyer">
  <svg class="flyer__accent" width="630" height="890" aria-hidden="true">
    <polygon points="0,210 50,210 50,345 0,345" fill="var(--navy)"/>
    <polygon points="0,210 50,210 0,345" fill="var(--navy-dark)"/>
    <rect x="255" y="258" width="375" height="20" fill="var(--navy)"/>
  </svg>

  <div class="photo photo--plumber" role="img" aria-label="Smiling plumber in a yellow hard hat and blue polo with arms crossed, wearing a tool belt"></div>

  <h1 class="brand">Marcus<br>Plumbing</h1>

  <div class="photo photo--thumb photo--under-sink" role="img" aria-label="Plumber working on pipes under a sink"></div>
  <div class="photo photo--thumb photo--pipe" role="img" aria-label="Hand tightening a chrome sink pipe with a red wrench"></div>

  <section class="panel panel--offer">
    <div class="panel__frame"></div>
    <h2 class="panel__tab">Offer</h2>
    <ul class="checklist">
      <li><svg width="24" height="26" viewBox="0 0 24 26"><path d="M2 14 L9 22 L22 2" fill="none" stroke="#fff" stroke-width="3.5" stroke-linecap="round"/></svg><span class="hl lead">15% off your overall bill</span><span class="lead">*</span></li>
      <li><svg width="24" height="26" viewBox="0 0 24 26"><path d="M2 14 L9 22 L22 2" fill="none" stroke="#fff" stroke-width="3.5" stroke-linecap="round"/></svg>No GST payable, saving you <span class="hl">additional 10% on your bill</span> ^</li>
      <li><svg width="24" height="26" viewBox="0 0 24 26"><path d="M2 14 L9 22 L22 2" fill="none" stroke="#fff" stroke-width="3.5" stroke-linecap="round"/></svg>Plus, a <span class="hl">FREE hot water health check</span> and replacement quote ~</li>
    </ul>
  </section>

  <section class="panel panel--services">
    <div class="panel__frame"></div>
    <h2 class="panel__tab">Services Offered</h2>
    <ul class="checklist">
      <li><svg width="24" height="26" viewBox="0 0 24 26"><path d="M2 14 L9 22 L22 2" fill="none" stroke="#fff" stroke-width="3.5" stroke-linecap="round"/></svg>All plumbing, draining, and gasfitting works</li>
      <li><svg width="24" height="26" viewBox="0 0 24 26"><path d="M2 14 L9 22 L22 2" fill="none" stroke="#fff" stroke-width="3.5" stroke-linecap="round"/></svg>Quality work at a Decent Price</li>
      <li><svg width="24" height="26" viewBox="0 0 24 26"><path d="M2 14 L9 22 L22 2" fill="none" stroke="#fff" stroke-width="3.5" stroke-linecap="round"/></svg>Local Plumber</li>
    </ul>
  </section>

  <div class="footer"></div>
  <div class="footer__rule"></div>
  <p class="cta">To make an appointment, <span class="hl">call or email Marcus,</span><br>or alternatively make a booking directly on the website</p>

  <p class="terms">*Offer valid between <b>15 August 2016 to 15 October 2016</b><br>^ Valid until <b>30 September 2016.</b><br>~ Quote valid for <b>12 months from the quote date.</b></p>

  <div class="contact">
    <p class="contact__phone"><svg width="20" height="20" viewBox="0 0 20 20" aria-hidden="true"><circle cx="10" cy="10" r="9" fill="none" stroke="#1f8fd8" stroke-width="1.6"/><path d="M6.5 5 L8.5 5 L9.2 7.6 L8 8.6 Q9 11 11.4 12 L12.4 10.8 L15 11.5 L15 13.5 Q13 15.5 9.5 13.6 Q5.5 11 5 7 Z" fill="#1f8fd8"/></svg>0400 128 640</p>
    <p class="contact__line">marcus@marcusplumbing.com</p>
    <p class="contact__line">www.marcusplumbing.com</p>
  </div>
</main>
</body>
</html>
```